Landing Page / Waitlist

I would like a landing page for people to sign up for a waiting list. The text on the page should include (but is not limited to):
1) Main point: The accounting system you'll love
2) Secondary points:
a. Ruthlessly efficient
b. Quietly intelligent
c. Driven by AI
I've attached a file of our logo

The design should be simple, clean, and innovative - this is an ai company

```html
<!DOCTYPE html>
<html lang="en">
<head>
<meta charset="utf-8">
<title>Tallyway — Join the Waitlist</title>
<link href="https://fonts.googleapis.com/css2?family=Plus+Jakarta+Sans:wght@400;500;600&display=swap" rel="stylesheet">
<style>
:root{
  --bg:#fbfbfb;
  --ink:#2d2d2d;
  --text:#333333;
  --muted:#7a7a7a;
  --accent:#1a9be8;
  --dark:#333333;
  --card:#ffffff;
  --field:#f3f3f3;
}
*{box-sizing:border-box;margin:0;padding:0}
html,body{width:1200px;height:1047px;overflow:hidden}
body{background:var(--bg);font-family:"Plus Jakarta Sans",sans-serif;color:var(--text);position:relative}
.brand{position:absolute;top:118px;left:0;width:1200px;display:flex;justify-content:center;align-items:center;gap:12px}
.brand-dot{width:28px;height:28px;border-radius:50%;background:var(--accent)}
.brand-name{font-size:40px;font-weight:600;color:var(--muted);letter-spacing:-1px}
.headline{position:absolute;top:192px;left:0;width:1200px;text-align:center;font-size:53px;font-weight:500;line-height:57px;color:var(--ink);letter-spacing:-0.5px}
.headline svg{width:34px;height:34px;vertical-align:-4px;margin-left:4px}
.features{position:absolute;top:381px;left:257px;display:flex;gap:9px}
.feature{position:relative;width:223px;height:123px;background:var(--card);border-radius:8px;box-shadow:0 6px 24px rgba(0,0,0,.06);text-align:center;padding-top:64px;font-size:17px}
.feature-icon{position:absolute;top:-35px;left:77px;width:69px;height:69px;border-radius:50%;background:var(--dark);display:flex;align-items:center;justify-content:center}
.feature-icon svg{width:28px;height:28px;fill:none;stroke:var(--accent);stroke-width:1.8;stroke-linecap:round;stroke-linejoin:round}
.tagline{position:absolute;top:562px;left:0;width:1200px;text-align:center;font-size:17.5px}
.signup{position:absolute;top:615px;left:370px;width:460px;height:60px;border-radius:30px;background:var(--field);border:1px solid #e6e6e6}
.signup-field{position:absolute;left:29px;top:19px;font-size:15.5px;color:#444}
.signup-button{position:absolute;right:4px;top:4px;width:200px;height:51px;border-radius:26px;background:var(--dark);color:#fff;font-size:15.5px;display:flex;align-items:center;justify-content:center;gap:16px}
.signup-button svg{width:18px;height:22px;fill:var(--accent)}
.crowd{position:absolute;top:686px;left:141px;width:918px;height:306px;background:linear-gradient(180deg,#f4f4f4,#e4e4e4);border-radius:8px 8px 0 0}
.footer{position:absolute;top:992px;left:0;width:1200px;height:55px;background:var(--dark);color:var(--accent);font-size:14px;display:flex;align-items:center;justify-content:center}
</style>
</head>
<body>
<div class="brand"><span class="brand-dot"></span><span class="brand-name">Tallyway</span></div>
<h1 class="headline">The Accounting System<br>You'll Love<svg viewBox="0 0 24 24"><path fill="#1a9be8" d="M12 21s-8-5.3-8-11a4.5 4.5 0 0 1 8-2.8A4.5 4.5 0 0 1 20 10c0 5.7-8 11-8 11z"/></svg></h1>
<div class="features">
  <div class="feature"><div class="feature-icon"><svg viewBox="0 0 24 24"><circle cx="12" cy="12" r="9"/><path d="M13 6l-4 7h4l-2 5"/></svg></div>Ruthlessly efficient</div>
  <div class="feature"><div class="feature-icon"><svg viewBox="0 0 24 24"><path d="M6 19v-3a7 7 0 1 1 12-5l1 3h-2v3h-4v2"/><circle cx="12" cy="10" r="2.5"/></svg></div>Quietly intelligent</div>
  <div class="feature"><div class="feature-icon"><svg viewBox="0 0 24 24"><rect x="6" y="4" width="12" height="7" rx="3"/><rect x="5" y="14" width="14" height="6" rx="2"/><path d="M10 7.5h.01M14 7.5h.01"/></svg></div>Driven Better by AI</div>
</div>
<p class="tagline">Join the waitlist today and be among the first to experience accounting done right.</p>
<div class="signup">
  <span class="signup-field">Your Email</span>
  <span class="signup-button">Join the Waitlist<svg viewBox="0 0 18 22"><path d="M2 0h14v3l-5 8 5 8v3H2v-3l5-8-5-8z"/></svg></span>
</div>
<div class="crowd" role="img" aria-label="Line illustration of five cheerful people giving thumbs up, pointing upward and making heart gestures"></div>
<footer class="footer">Copyright © 2025 Tallyway. All rights reserved.</footer>
</body>
</html>
```